Web Design For Marlow Pool Service

We are working with a company that wants a website for their pool service. Some sites to use for content/competitors and inspiration:
https://sacramento.brightwaterpoolco.example/builder/newbuild/repair/ppc
https://hollowbrookpoolcareplus.example/
https://lakemontpoolservice.example/
https://www.dravenspoolresurfacing.example/pool-renovation-ga/
Thank you for taking the time to consider designing a website for us. We are web developers based in Stockton, CA, USA. Most of our projects go through the same process. Understanding this process may help you win a project with us. We custom-code all of our websites in-house. We don’t have any requirements as to what tools you use for your design, but we prefer Figma files. For any design that we label as four-stars, we send it to the client for review. The client picks the final design they want us to use. Once we complete this process, we will continue to show additional clients all the four-star sites and purchase them later. Your designs will have multiple chances to sell. For better chances of success, we ask that you follow these guidelines.
IMAGES:
If you use any images or icons in the design, we ask that you have a link to the asset so we can purchase the image/icon. Most of the designs we submit do not have the customer’s images on them unless they have some great images. Be creative; show us the feeling you are trying to portray with your image choices. Use any royalty-free site you choose. We subscribe to Adobe and mainly use their images, but we can purchase images outside of Adobe. PLEASE NOTE: we will not submit designs to clients with watermarks on the images.
FONTS:
We ask that you identify the fonts used in the design. This can be done in a message if you want. We typically use Google Fonts and Adobe Fonts.
CONTENT:
We're always open to different content and ideas. We often submit designs with stock images so the client can see our vision. We typically take pictures after the website launch to use their images with our vision. Lorem Ipsum is fine for paragraphs, but we ask that you write the headers in correct English. We want to be able to show the vision and identify the sections of the website.
INSPIRATION:
We typically add a couple of links in the brief of websites we like to help you get started in your design.
REVISIONS:
We do not often ask for revisions of the designs unless we see something in the design that may not appeal to the client. If there are slight changes that we want to make, we do that in the development process.
FEEDBACK:
We rarely give feedback on designs during the design process. We are working on many website projects and do not have the time to provide feedback. We usually respond if your request is well thought out and asks specific questions, but a note asking “feedback, please” usually goes unanswered.
Number of Pages Required
1 page
Look and feel
Each slider illustrates characteristics of the customer's brand and the style your logo design should communicate.

```html
<!DOCTYPE html>
<html lang="en">
<head>
<meta charset="utf-8">
<title>Marlow Pool Service</title>
<link href="https://fonts.googleapis.com/css2?family=Cinzel:wght@400;600;700&family=EB+Garamond:wght@400;500&family=Lato:wght@400;700&display=swap" rel="stylesheet">
<style>
:root{
  --blue:#2f9cf6;
  --blue-deep:#1a7fd8;
  --ink:#575757;
  --text:#444;
  --bar:#5a5a5a;
  --footer:#5f5f5f;
  --white:#fff;
  --star:#f6a623;
}
*{margin:0;padding:0;box-sizing:border-box}
html,body{width:1200px;height:3174px;overflow:hidden;background:var(--white)}
body{position:relative;font-family:'Lato',sans-serif;color:var(--text)}
.abs{position:absolute}

.topbar{left:0;top:0;width:1200px;height:59px;background:var(--bar);color:var(--white);font-size:12.5px;font-weight:700;text-align:center;line-height:59px;letter-spacing:.2px}

.hero{left:0;top:59px;width:1200px;height:653px;background:var(--blue);overflow:hidden}
.brand{color:var(--white);font-family:'Cinzel',serif;font-weight:400;line-height:1}
.brand .name{display:block;font-size:42px;letter-spacing:2px}
.brand .sub{display:block;font-size:22px;letter-spacing:5px;margin-top:4px;padding-left:46px}
.hero .brand{left:111px;top:40px}
.menu{left:1064px;top:42px;width:26px;height:28px}
.hero-photo{left:65px;top:282px;width:549px;height:306px;background:linear-gradient(180deg,rgba(47,156,246,0) 60%,var(--blue) 100%),linear-gradient(115deg,#1c3c78 0%,#b0203a 35%,#c3283e 50%,#2d6cc0 72%,#3b8fe0 100%)}
.hero h1{left:108px;top:174px;width:520px;font-family:'Cinzel',serif;font-weight:700;font-size:61px;line-height:78px;color:var(--white);letter-spacing:1px}
.hero .lede{left:111px;top:411px;width:460px;font-size:15.5px;font-weight:700;line-height:31px;color:var(--white)}
.promo{overflow:hidden}
.promo .img{position:absolute;left:0;top:0;width:100%;height:100%}
.promo h3{position:absolute;left:20px;font-family:'Cinzel',serif;font-weight:700;font-size:17px;line-height:31px;color:var(--white);letter-spacing:.5px}
.promo svg{position:absolute;left:20px}
.promo-a{left:643px;top:112px;width:261px;height:433px}
.promo-a .img{background:linear-gradient(180deg,#4f8a3a 0%,#3aa2e6 12%,#1aa7ef 38%,#e8e6df 43%,#9a9a98 58%,var(--blue) 88%)}
.promo-a h3{top:321px}
.promo-a svg{top:393px}
.promo-b{left:928px;top:194px;width:262px;height:418px}
.promo-b .img{background:linear-gradient(180deg,#3b8fd6 0%,#7fb9e6 30%,#d7a383 38%,#2eaed8 55%,var(--blue) 85%)}
.promo-b h3{top:309px}
.promo-b svg{top:380px}

.heading{left:0;width:1200px;text-align:center;font-family:'Cinzel',serif;font-weight:600;font-size:42px;color:var(--ink);letter-spacing:1.5px}
.heading .hl{color:var(--blue)}
.about-h{top:770px}
.para{text-align:center;font-size:15.5px;line-height:31px;color:var(--text)}
.para-1{left:155px;top:844px;width:890px}
.para-2{left:165px;top:967px;width:870px}
.btn{background:var(--blue);color:var(--white);font-family:'Cinzel',serif;font-weight:700;font-size:19px;text-align:center;line-height:51px;letter-spacing:1px}
.btn-contact{left:514px;top:1053px;width:172px;height:51px}

.services-h{top:1156px}
.ph{position:absolute}
.svc{position:absolute;width:326px;text-align:center}
.svc .num{font-family:'Cinzel',serif;font-size:23px;color:var(--blue);line-height:1}
.svc h3{font-family:'EB Garamond',serif;font-weight:500;font-size:26px;color:#222;margin-top:10px;line-height:1.2}
.svc p{font-size:14px;line-height:26px;color:var(--text);margin:6px auto 0;width:280px}
.svc a{display:inline-block;margin-top:4px;font-size:14px;color:#222;text-decoration:underline}
.ph-1{left:111px;top:1257px;width:325px;height:256px;background:linear-gradient(135deg,#1f5f9a,#3a8ccc 45%,#6fb5dc 70%,#235f90)}
.ph-2{left:436px;top:1450px;width:325px;height:256px;background:linear-gradient(160deg,#c9b6a4 0%,#9fb8c8 25%,#4f9ac9 55%,#b9d6e6 80%,#3f7fb0)}
.ph-3{left:761px;top:1257px;width:328px;height:256px;background:linear-gradient(150deg,#e4eef3 0%,#4aa7e0 30%,#1d5fb0 55%,#2f87d3 75%,#86b3c9)}
.svc-1{left:111px;top:1534px}
.svc-2{left:436px;top:1253px;background:var(--white);height:197px}
.svc-3{left:761px;top:1534px}

.ba{top:1797px;width:600px;height:465px}
.before{left:0;background:linear-gradient(180deg,#5c5a4c 0%,#8e8a78 18%,#9aa3a6 35%,#6f7a7e 60%,#2c3130 100%)}
.after{left:600px;background:linear-gradient(180deg,#3e6a8e 0%,#2e5a2e 15%,#3d6e34 45%,#38d6ef 62%,#22c2e0 75%,#8c7a70 88%,#6e6058 100%)}
.tag{top:1836px;height:45px;line-height:45px;font-family:'Cinzel',serif;font-weight:700;font-size:30px;color:var(--white);text-align:center;letter-spacing:1px}
.tag-before{left:41px;width:144px;background:#5f5f5f}
.tag-after{left:637px;width:124px;background:var(--blue)}

.reviews-h{top:2310px}
.card{top:2395px;width:300px;height:202px;background:var(--white);box-shadow:0 3px 14px rgba(0,0,0,.12)}
.card .avatar{position:absolute;left:9px;top:12px;width:64px;height:64px;border-radius:50%;background:linear-gradient(180deg,#d9d9d9,#a8a8a8)}
.card .stars{position:absolute;left:95px;top:14px;color:var(--star);font-size:11px;letter-spacing:1px}
.card .who{position:absolute;left:94px;top:38px;font-size:17px;font-weight:700;color:#222}
.card .date{position:absolute;left:95px;top:67px;font-size:10px;color:#8a8a8a}
.card p{position:absolute;left:12px;top:100px;width:280px;font-size:13.5px;line-height:26px;color:#555}
.card-1{left:111px}.card-2{left:448px}.card-3{left:788px}
.card-2 p{color:#333}
.btn-more{left:514px;top:2655px;width:172px;height:51px}

.footer{left:0;top:2771px;width:1200px;height:403px;background:var(--footer)}
.social{top:2965px;width:32px;height:32px;border-radius:50%;background:var(--white)}
.col-h{top:2845px;font-family:'Cinzel',serif;font-size:18px;font-weight:600;color:var(--white);letter-spacing:.5px}
.links{list-style:none}
.links li{height:34.3px;font-size:15px;color:var(--white);display:flex;align-items:center;gap:10px}
.contact-row{display:flex;align-items:center;gap:14px;color:var(--white);font-size:15px;line-height:27px}
.contact-row .ico{width:32px;height:32px;border-radius:50%;background:var(--white);flex:none;display:flex;align-items:center;justify-content:center}
.rule{left:111px;top:3092px;width:978px;height:1px;background:#cfcfcf}
.copy{left:0;top:3128px;width:1200px;text-align:center;font-size:15px;color:var(--white)}
</style>
</head>
<body>

<div class="abs topbar">ITAQUE EARUM RERUM HIC TENETUR A SAPIENTE DELECTUS, UT AUT REICIENDIS</div>

<section class="abs hero">
  <div class="abs brand"><span class="name">MARLOW</span><span class="sub">POOL SERVICE</span></div>
  <svg class="abs menu" viewBox="0 0 26 28" aria-label="Menu"><g stroke="#fff" stroke-width="2"><line x1="0" y1="2" x2="26" y2="2"/><line x1="4" y1="14" x2="26" y2="14"/><line x1="0" y1="26" x2="26" y2="26"/></g></svg>
  <div class="abs hero-photo" role="img" aria-label="Photo of a swimmer in a red swimsuit gliding underwater"></div>
  <h1 class="abs">BRING YOUR DREAM POOL TO LIFE</h1>
  <p class="abs lede">Itaque earum rerum hic tenetur a sapiente delectus, ut aut reiciendis voluptatibus maiores alias consequatur aut perferendis doloribus asperiores repellat.</p>

  <div class="abs promo promo-a">
    <div class="img" role="img" aria-label="Photo of a clean rectangular backyard pool with stone deck"></div>
    <h3>TEMPORIBUS AUTEM QUIBUSDAM</h3>
    <svg width="18" height="24" viewBox="0 0 18 24"><g stroke="#fff" stroke-width="1.5" fill="none"><line x1="9" y1="1" x2="9" y2="22"/><polyline points="2,15 9,22 16,15"/></g></svg>
  </div>
  <div class="abs promo promo-b">
    <div class="img" role="img" aria-label="Photo of a child smiling while swimming in a pool"></div>
    <h3>OFFICIIS DEBITIS AUT NECESSITATIBUS</h3>
    <svg width="18" height="24" viewBox="0 0 18 24"><g stroke="#fff" stroke-width="1.5" fill="none"><line x1="9" y1="1" x2="9" y2="22"/><polyline points="2,15 9,22 16,15"/></g></svg>
  </div>
</section>

<h2 class="abs heading about-h"><span class="hl">ABOUT MARLOW</span> POOL SERVICE</h2>
<p class="abs para para-1">Nam libero tempore, cum soluta nobis est eligendi optio cumque nihil impedit quo minus id quod maxime placeat facere possimus, omnis voluptas assumenda est, omnis dolor repellendus. Temporibus autem quibusdam et aut officiis debitis aut rerum necessitatibus saepe eveniet ut et voluptates repudiandae sint et molestiae non recusandae.</p>
<p class="abs para para-2">Itaque earum rerum hic tenetur a sapiente delectus, ut aut reiciendis voluptatibus maiores alias consequatur aut perferendis doloribus asperiores repellat.</p>
<div class="abs btn btn-contact">CONTACT US</div>

<h2 class="abs heading services-h"><span class="hl">OUR</span> POOL SERVICE</h2>
<div class="ph ph-1" role="img" aria-label="Photo of a hand holding a water testing meter above a pool"></div>
<div class="ph ph-3" role="img" aria-label="Photo of a technician servicing a pool pump beside the water"></div>
<div class="ph ph-2" role="img" aria-label="Photo of an automatic pool cleaner with hose in the water"></div>

<div class="svc svc-1"><div class="num">01</div><h3>Temporibus autem quibus</h3><p>Temporibus autem quibusdam et aut officiis debitis aut rerum necessitatibus saepe eveniet</p><a>Learn More</a></div>
<div class="svc svc-2"><div class="num">02</div><h3>Mporibus autem quibus</h3><p>Temporibus autem quibusdam et aut officiis debitis aut rerum necessitatibus saepe eveniet</p><a>Learn More</a></div>
<div class="svc svc-3"><div class="num">03</div><h3>Emporibus autem quibus</h3><p>Temporibus autem quibusdam et aut officiis debitis aut rerum necessitatibus saepe eveniet</p><a>Learn More</a></div>

<div class="abs ba before" role="img" aria-label="Photo of a neglected, murky abandoned pool before renovation"></div>
<div class="abs ba after" role="img" aria-label="Photo of a restored turquoise pool surrounded by trees and paving"></div>
<div class="abs tag tag-before">BEFORE</div>
<div class="abs tag tag-after">AFTER</div>

<h2 class="abs heading reviews-h"><span class="hl">WHAT</span> CUSTOMER SAYS</h2>
<div class="abs card card-1">
  <div class="avatar" role="img" aria-label="Customer portrait"></div>
  <div class="stars">★★★★★</div><div class="who">Daniel Harwick</div><div class="date">April 12, 2023</div>
  <p>Temporibus autem quibusdam et aut offici-is debitis aut rerum necessitatibus saepe eveniet ut et voluptates nt et moles tiae non recusandae.</p>
</div>
<div class="abs card card-2">
  <div class="avatar" role="img" aria-label="Customer portrait"></div>
  <div class="stars">★★★★★</div><div class="who">Stefan Morrow</div><div class="date">March 3, 2023</div>
  <p>Itaque earum rerum hic tenetur a sapiente delectus, ut aut reiciendis voluptatibus maiores alias consequatur aut perferendis doloribus asperiores repellat.</p>
</div>
<div class="abs card card-3">
  <div class="avatar" role="img" aria-label="Customer portrait"></div>
  <div class="stars">★★★★★</div><div class="who">Elena Tarrant</div><div class="date">August 24, 2023</div>
  <p>Nam libero tempore, cum soluta nobis est eligendi optio cumque nihil impedit quo minus id quod maxime placeat facere maxime placea possimus.</p>
</div>
<div class="abs btn btn-more">VIEW MORE</div>

<footer class="abs footer"></footer>
<div class="abs brand" style="left:115px;top:2876px"><span class="name">MARLOW</span><span class="sub">POOL SERVICE</span></div>
<div class="abs social" style="left:111px"></div>
<div class="abs social" style="left:169px"></div>
<div class="abs social" style="left:227px"></div>
<div class="abs social" style="left:285px"></div>

<div class="abs col-h" style="left:430px">QUICK LINKS</div>
<ul class="abs links" style="left:430px;top:2882px">
  <li><svg width="14" height="12" viewBox="0 0 14 12"><path d="M0 4.5h8V0l6 6-6 6V7.5H0z" fill="#fff"/></svg>Home</li>
  <li><svg width="14" height="12" viewBox="0 0 14 12"><path d="M0 4.5h8V0l6 6-6 6V7.5H0z" fill="#fff"/></svg>About</li>
  <li><svg width="14" height="12" viewBox="0 0 14 12"><path d="M0 4.5h8V0l6 6-6 6V7.5H0z" fill="#fff"/></svg>Services</li>
  <li><svg width="14" height="12" viewBox="0 0 14 12"><path d="M0 4.5h8V0l6 6-6 6V7.5H0z" fill="#fff"/></svg>Testimonials</li>
  <li><svg width="14" height="12" viewBox="0 0 14 12"><path d="M0 4.5h8V0l6 6-6 6V7.5H0z" fill="#fff"/></svg>Contact Us</li>
</ul>

<div class="abs col-h" style="left:663px">HELP LINKS</div>
<ul class="abs links" style="left:663px;top:2882px">
  <li><svg width="14" height="12" viewBox="0 0 14 12"><path d="M0 4.5h8V0l6 6-6 6V7.5H0z" fill="#fff"/></svg>FAQ</li>
  <li><svg width="14" height="12" viewBox="0 0 14 12"><path d="M0 4.5h8V0l6 6-6 6V7.5H0z" fill="#fff"/></svg>Terms of use</li>
  <li><svg width="14" height="12" viewBox="0 0 14 12"><path d="M0 4.5h8V0l6 6-6 6V7.5H0z" fill="#fff"/></svg>Privacy Policy</li>
  <li><svg width="14" height="12" viewBox="0 0 14 12"><path d="M0 4.5h8V0l6 6-6 6V7.5H0z" fill="#fff"/></svg>Support Links</li>
  <li><svg width="14" height="12" viewBox="0 0 14 12"><path d="M0 4.5h8V0l6 6-6 6V7.5H0z" fill="#fff"/></svg>Conditions</li>
</ul>

<div class="abs col-h" style="left:893px">CONTACT US</div>
<div class="abs contact-row" style="left:893px;top:2895px">
  <span class="ico"><svg width="14" height="18" viewBox="0 0 14 18"><path d="M7 0C3.1 0 0 3 0 6.8 0 11.5 7 18 7 18s7-6.5 7-11.2C14 3 10.9 0 7 0zm0 9.5A2.6 2.6 0 1 1 7 4.3a2.6 2.6 0 0 1 0 5.2z" fill="#5f5f5f"/></svg></span>
  <span>Marlow Pool Service<br>United States</span>
</div>
<div class="abs contact-row" style="left:893px;top:2955px">
  <span class="ico"><svg width="16" height="16" viewBox="0 0 24 24"><path d="M6.6 10.8a15.1 15.1 0 0 0 6.6 6.6l2.2-2.2c.3-.3.7-.4 1-.2 1.1.4 2.3.6 3.6.6.6 0 1 .4 1 1V20c0 .6-.4 1-1 1A17 17 0 0 1 3 4c0-.6.4-1 1-1h3.5c.6 0 1 .4 1 1 0 1.3.2 2.5.6 3.6.1.3 0 .7-.2 1z" fill="#5f5f5f"/></svg></span>
  <span>+1 555 014 2277</span>
</div>
<div class="abs contact-row" style="left:893px;top:3007px">
  <span class="ico"><svg width="16" height="12" viewBox="0 0 16 12"><rect width="16" height="12" rx="1.5" fill="#5f5f5f"/><polyline points="1,1.5 8,7 15,1.5" stroke="#fff" stroke-width="1.3" fill="none"/></svg></span>
  <span>info@marlowpools.example</span>
</div>

<div class="abs rule"></div>
<div class="abs copy">Copyrights@2024.Marlow Pool Service.All Rights Reserved</div>

</body>
</html>
```